Delivery Performance Dashboard for Web Portal

We need you to design a dashboard for our web portal. We deliver sand and stone to construction jobsites. The attached screenshot is from our current web portal dashboard . It shows how much material has been delivered from an order.

Dump trucks will deliver multiple loads during the day and the dispatcher uses the dashboard to monitor if they need to add more trucks or less trucks to fulfill the order. An example would be, I need to ship 1,000 tons of sand to a jobsite and I plan to use 10 trucks during the day and that it will take 10 hours of hauling to complete the job. After 5 hours of hauling (50% the day is over), I should have delivered 500 tons of sand (50% of the order). But maybe there is a lot of traffic, and I only have delivered 300 tons. The dashboard will show that I am behind schedule and I might need to add 2 more trucks to the job.

Industry/Entity Type

Construction

Font styles to use
Sans Serif

Requirements
Must have
• We need a progress bar showing how much material has been delivered, how much material was requested to be delivered total and how much material should have been delivered at the current time. The goal is to show the user if the deliveries are ahead or behind the expected pace and why.
Nice to have
• The icons for plant, driving and jobsite show if the actual times have exceeded or beaten the planned times. Maybe you have other ideas to show the user if the trucks are sitting longer on the jobsite, at the plant to get loaded or driving to and from the jobsite.

```html
<!DOCTYPE html>
<html lang="en">
<head>
<meta charset="utf-8">
<title>Delivery Performance Dashboard</title>
<link href="https://fonts.googleapis.com/css2?family=Poppins:wght@400;500;600&display=swap" rel="stylesheet">
<style>
:root{
  --bg:#eef4fc;
  --panel:#ffffff;
  --head-a:#7467d6;
  --head-b:#4a90e8;
  --table-head:#5b7fdc;
  --ink:#333a44;
  --muted:#6b7079;
  --rule:#e3e7ee;
  --blue:#1a73e8;
  --red:#dc3545;
  --green:#28a745;
  --yellow:#ffc107;
  --teal:#17a2b8;
  --orange:#fd7e14;
  --icon:#8a8f98;
  --progress:#6b6fd6;
}
*{box-sizing:border-box;margin:0;padding:0}
html,body{width:1200px;height:796px;overflow:hidden;background:var(--bg)}
body{font-family:'Poppins',sans-serif;color:var(--ink)}
.canvas{position:relative;width:1200px;height:796px;overflow:hidden;background:var(--bg)}
.abs{position:absolute}
.topbar{position:absolute;left:0;top:0;width:1200px;height:40px;background:linear-gradient(90deg,var(--head-a),var(--head-b))}
.brand{left:14px;top:8px;font-size:17px;font-weight:500;color:#fff}
.search{left:866px;top:7px;width:159px;height:25px;background:#fff;border-radius:3px;font-size:9px;color:#c4c8cf;padding:6px 0 0 26px}
.search svg{position:absolute;left:8px;top:7px}
.avatar{left:1118px;top:4px;width:32px;height:32px;border-radius:50%;background:linear-gradient(135deg,#b86a43,#5b3a2a);border:2px solid #fff}
.badge{left:1090px;top:10px;width:10px;height:10px;border-radius:50%;background:#f0616b;color:#fff;font-size:7px;text-align:center;line-height:10px}
.slogan{left:21px;top:70px;font-size:19px;font-weight:600;color:#2f3540}
.table{left:16px;top:117px;width:1176px;height:333px;background:var(--panel)}
.thead{position:absolute;left:0;top:0;width:1176px;height:50px;background:var(--table-head)}
.th{position:absolute;top:18px;font-size:11px;color:#fff;display:flex;align-items:center;gap:8px}
.row{position:absolute;left:0;width:1176px;font-size:10px}
.row .c{position:absolute}
.rule{position:absolute;left:2px;width:1172px;height:1px;background:var(--rule)}
.tons-bar{position:absolute;left:694px;width:187px;height:6px;border:1px solid var(--table-head);border-radius:3px;overflow:hidden}
.tons-bar i{display:block;height:100%;background:var(--progress)}
.tons-txt{font-size:9px}
.ahead{color:var(--green)}
.behind{color:var(--red)}
.card{position:absolute;background:var(--panel)}
.card h3{position:absolute;left:15px;top:12px;font-size:14px;font-weight:500}
.card .sub{position:absolute;left:15px;top:33px;font-size:9px;color:var(--muted)}
.close{position:absolute;font-size:11px;color:#444;font-weight:600}
.lbl{position:absolute;font-size:10.5px;color:var(--muted)}
.lbl b{font-weight:500;color:#444}
.bar{position:absolute;height:6px;border-radius:3px}
.val{position:absolute;font-size:10px;color:var(--muted)}
.cat{position:absolute;left:12px;top:60px;font-size:11px;color:var(--muted);display:flex;align-items:center;gap:6px}
</style>
</head>
<body>
<svg width="0" height="0" style="position:absolute">
  <defs>
    <symbol id="sort" viewBox="0 0 8 18"><path d="M1 6l3-3 3 3M1 12l3 3 3-3" fill="none" stroke="#fff" stroke-width="1.4"/></symbol>
    <symbol id="factory" viewBox="0 0 16 14"><path d="M0 14V2h3v6l4-3v3l4-3v3l5-3v9z" fill="currentColor"/></symbol>
    <symbol id="truck" viewBox="0 0 20 14"><path d="M0 1h12v9H0zM12 4h4l4 4v2h-8z" fill="currentColor"/><circle cx="4" cy="11.5" r="2.3" fill="currentColor" stroke="#fff"/><circle cx="15" cy="11.5" r="2.3" fill="currentColor" stroke="#fff"/></symbol>
    <symbol id="pin" viewBox="0 0 12 16"><path d="M6 0a6 6 0 0 1 6 6c0 4-6 10-6 10S0 10 0 6a6 6 0 0 1 6-6z" fill="currentColor"/><circle cx="6" cy="6" r="2.2" fill="#fff"/></symbol>
    <symbol id="up" viewBox="0 0 6 4"><path d="M0 4l3-4 3 4z" fill="#dc3545"/></symbol>
    <symbol id="down" viewBox="0 0 6 4"><path d="M0 0l3 4 3-4z" fill="#28a745"/></symbol>
  </defs>
</svg>
<div class="canvas">
  <header class="topbar">
    <div class="abs brand">Your Logo</div>
    <div class="abs search"><svg width="11" height="11" viewBox="0 0 12 12"><circle cx="5" cy="5" r="4" fill="none" stroke="#777" stroke-width="1.5"/><path d="M8 8l3.5 3.5" stroke="#777" stroke-width="1.5"/></svg>Search...</div>
    <svg class="abs" style="left:1040px;top:13px" width="16" height="14" viewBox="0 0 16 14"><path d="M1 1h14v9H6l-3 3v-3H1z" fill="none" stroke="#fff" stroke-width="1.5"/><path d="M4 4.5h8M4 7h6" stroke="#fff" stroke-width="1.2"/></svg>
    <svg class="abs" style="left:1076px;top:12px" width="15" height="16" viewBox="0 0 15 16"><path d="M7.5 1a4.5 4.5 0 0 1 4.5 4.5V10l2 2H1l2-2V5.5A4.5 4.5 0 0 1 7.5 1zM5.5 13.5a2 2 0 0 0 4 0" fill="none" stroke="#fff" stroke-width="1.5"/></svg>
    <div class="abs badge">2</div>
    <div class="abs avatar" role="img" aria-label="User profile photo"></div>
    <svg class="abs" style="left:1165px;top:14px" width="14" height="12" viewBox="0 0 14 12"><path d="M1 1h12M4 4.3h9M1 7.6h12M4 11h9" stroke="#fff" stroke-width="1.5"/></svg>
  </header>

  <h1 class="abs slogan">Header Slogan Goes Here</h1>

  <section class="abs table">
    <div class="thead">
      <div class="th" style="left:9px">Order <svg width="8" height="18"><use href="#sort"/></svg></div>
      <div class="th" style="left:97px">Origin <svg width="8" height="18"><use href="#sort"/></svg></div>
      <div class="th" style="left:255px">Destination <svg width="8" height="18"><use href="#sort"/></svg></div>
      <div class="th" style="left:417px">Customer <svg width="8" height="18"><use href="#sort"/></svg></div>
      <div class="th" style="left:619px">Status <svg width="8" height="18"><use href="#sort"/></svg></div>
      <div class="th" style="left:695px">Tons <svg width="8" height="18" style="margin-left:14px"><use href="#sort"/></svg></div>
      <div class="th" style="left:906px">Wait Times <svg width="8" height="18"><use href="#sort"/></svg></div>
      <div class="th" style="left:1028px">Remaining <svg width="8" height="18"><use href="#sort"/></svg></div>
      <div class="th" style="left:1126px">+/− <svg width="12" height="9" viewBox="0 0 20 14" style="color:#fff"><use href="#truck"/></svg></div>
    </div>

    <!-- rows -->
    <div class="row" style="top:76px">
      <span class="c" style="left:22px;top:6px">177746</span>
      <span class="c" style="left:96px;top:6px">Calder Asphalt Plant</span>
      <span class="c" style="left:252px;top:6px">BZJV-185 from mm 77-98</span>
      <span class="c" style="left:413px;top:6px">Harlan Paving - North Division</span>
      <span class="c" style="left:618px;top:6px">Accepted</span>
      <div class="tons-bar" style="top:0"><i style="width:45%"></i></div>
      <span class="c tons-txt" style="left:694px;top:12px">722.57 / 1500</span>
      <span class="c tons-txt" style="left:795px;top:12px">7:30 am - 5:00 pm</span>
      <span class="c" style="left:906px;top:8px;color:var(--icon)"><svg width="10" height="9"><use href="#factory"/></svg> <svg width="6" height="4"><use href="#up"/></svg> &nbsp;<svg width="13" height="9"><use href="#truck"/></svg> <svg width="6" height="4"><use href="#up"/></svg> &nbsp;<svg width="7" height="9"><use href="#pin"/></svg> <svg width="6" height="4"><use href="#down"/></svg></span>
      <span class="c ahead" style="left:1029px;top:6px">+1:25 hrs</span>
      <span class="c behind" style="left:1126px;top:6px">-31</span>
    </div>
    <div class="rule" style="top:118px"></div>

    <div class="row" style="top:138px">
      <span class="c" style="left:22px;top:6px">177746</span>
      <span class="c" style="left:96px;top:6px">Calder Asphalt Plant</span>
      <span class="c" style="left:252px;top:6px">BZJV-185 from mm 77-98</span>
      <span class="c" style="left:413px;top:6px">Harlan Paving - North Division</span>
      <span class="c" style="left:618px;top:6px">Accepted</span>
      <div class="tons-bar" style="top:0"><i style="width:54%"></i></div>
      <span class="c tons-txt" style="left:694px;top:12px">722.57 / 1500</span>
      <span class="c tons-txt" style="left:795px;top:12px">7:30 am - 5:00 pm</span>
      <span class="c" style="left:906px;top:8px;color:var(--icon)"><svg width="10" height="9"><use href="#factory"/></svg> <svg width="6" height="4"><use href="#up"/></svg> &nbsp;<svg width="13" height="9"><use href="#truck"/></svg> <svg width="6" height="4"><use href="#up"/></svg> &nbsp;<svg width="7" height="9"><use href="#pin"/></svg> <svg width="6" height="4"><use href="#down"/></svg></span>
      <span class="c ahead" style="left:1029px;top:6px">+1:25 hrs</span>
      <span class="c behind" style="left:1126px;top:6px">-31</span>
    </div>
    <div class="rule" style="top:179px"></div>

    <div class="row" style="top:200px">
      <span class="c" style="left:22px;top:6px">177746</span>
      <span class="c" style="left:96px;top:6px">Calder Asphalt Plant</span>
      <span class="c" style="left:252px;top:6px">BZJV-185 from mm 77-98</span>
      <span class="c" style="left:413px;top:6px">Harlan Paving - North Division</span>
      <span class="c" style="left:618px;top:6px">Accepted</span>
      <div class="tons-bar" style="top:0"><i style="width:62%"></i></div>
      <span class="c tons-txt" style="left:694px;top:12px">722.57 / 1500</span>
      <span class="c tons-txt" style="left:795px;top:12px">7:30 am - 5:00 pm</span>
      <span class="c" style="left:906px;top:8px;color:var(--icon)"><svg width="10" height="9"><use href="#factory"/></svg> <svg width="6" height="4"><use href="#up"/></svg> &nbsp;<svg width="13" height="9"><use href="#truck"/></svg> <svg width="6" height="4"><use href="#up"/></svg> &nbsp;<svg width="7" height="9"><use href="#pin"/></svg> <svg width="6" height="4"><use href="#down"/></svg></span>
      <span class="c ahead" style="left:1029px;top:6px">+1:25 hrs</span>
      <span class="c behind" style="left:1126px;top:6px">-31</span>
    </div>
    <div class="rule" style="top:245px"></div>

    <div class="row" style="top:262px">
      <span class="c" style="left:22px;top:6px">177746</span>
      <span class="c" style="left:96px;top:6px">Calder Asphalt Plant</span>
      <span class="c" style="left:252px;top:6px">BZJV-185 from mm 77-98</span>
      <span class="c" style="left:413px;top:6px">Harlan Paving - North Division</span>
      <span class="c" style="left:618px;top:6px">Accepted</span>
      <div class="tons-bar" style="top:0"><i style="width:0"></i></div>
      <span class="c tons-txt" style="left:694px;top:12px">722.57 / 1500</span>
      <span class="c tons-txt" style="left:795px;top:12px">7:30 am - 5:00 pm</span>
      <span class="c" style="left:906px;top:8px;color:var(--icon)"><svg width="10" height="9"><use href="#factory"/></svg> <svg width="6" height="4"><use href="#up"/></svg> &nbsp;<svg width="13" height="9"><use href="#truck"/></svg> <svg width="6" height="4"><use href="#up"/></svg> &nbsp;<svg width="7" height="9"><use href="#pin"/></svg> <svg width="6" height="4"><use href="#down"/></svg></span>
      <span class="c ahead" style="left:1029px;top:6px">+1:25 hrs</span>
      <span class="c behind" style="left:1126px;top:6px">-31</span>
    </div>
  </section>

  <!-- schedule card -->
  <section class="card" style="left:15px;top:463px;width:583px;height:311px">
    <h3>Order 17746</h3>
    <div class="sub">Genral Schedule vs Current Schedule</div>
    <span class="close" style="left:563px;top:10px">×</span>
    <div class="lbl" style="left:21px;top:60px;font-size:11px;display:flex;gap:8px;align-items:center"><svg width="17" height="13" viewBox="0 0 17 13"><path d="M1 0v12h16" fill="none" stroke="#8a8f98" stroke-width="1.6"/><path d="M3 10l4-5 3 3 5-6" fill="none" stroke="#8a8f98" stroke-width="1.6"/></svg>Schedule Average</div>
    <div class="lbl" style="left:21px;top:92px">Scheduled Load: <b>1500 ton</b></div>
    <div class="lbl" style="left:21px;top:113px">Esitamated Time: <b>3 hrs 25 mins</b></div>
    <div class="lbl" style="left:21px;top:139px">Materials Delivered</div>
    <div class="bar" style="left:22px;top:162px;width:84px;background:var(--blue);border-radius:3px 0 0 3px"></div>
    <div class="bar" style="left:106px;top:162px;width:71px;background:var(--red);border-radius:0 3px 3px 0"></div>
    <div class="lbl" style="left:30px;top:172px">800</div>
    <div class="lbl" style="left:131px;top:172px">700</div>
    <div class="lbl" style="left:22px;top:196px">Time Taken</div>
    <div class="bar" style="left:22px;top:221px;width:94px;background:var(--orange);border-radius:3px 0 0 3px"></div>
    <div class="bar" style="left:116px;top:221px;width:61px;background:var(--red);border-radius:0 3px 3px 0"></div>
    <div class="lbl" style="left:26px;top:234px"><b>2 hrs 35 mins</b></div>
    <div class="lbl" style="left:114px;top:234px"><b>1 hrs 10 mins</b></div>
    <div class="lbl" style="left:23px;top:266px">Ahead/Behind Schedule : &nbsp;<span style="color:var(--red);font-weight:500">45 mins</span> <span style="color:var(--red)">↓</span></div>
    <div class="lbl" style="left:22px;top:286px">To Meet Schedule Need More Trucks : &nbsp;<span style="color:var(--red);font-weight:500">3</span></div>

    <svg class="abs" style="left:0;top:0" width="583" height="311" viewBox="0 0 583 311" font-family="Poppins, sans-serif" font-size="10.5" fill="#6b7079">
      <rect x="311" y="19" width="10" height="10" fill="#28a745"/>
      <text x="330" y="28" font-size="9">Esitmated Schedule</text>
      <rect x="431" y="19" width="10" height="10" fill="#dc3545"/>
      <text x="448" y="28" font-size="9">Current Schedule</text>
      <g stroke="#dcdfe4" stroke-width="1.2">
        <line x1="270" y1="58" x2="555" y2="58"/>
        <line x1="270" y1="100" x2="555" y2="100"/>
        <line x1="270" y1="142" x2="555" y2="142"/>
        <line x1="270" y1="184" x2="555" y2="184"/>
        <line x1="270" y1="226" x2="555" y2="226"/>
        <line x1="270" y1="261" x2="555" y2="261"/>
      </g>
      <text x="236" y="62">5 hr</text>
      <text x="236" y="104">4 hr</text>
      <text x="236" y="146">3 hr</text>
      <text x="236" y="188">2 hr</text>
      <text x="238" y="230">1 hr</text>
      <text x="273" y="282">0</text>
      <text x="328" y="282">500</text>
      <text x="386" y="282">1000</text>
      <text x="451" y="282">1500</text>
      <text x="533" y="282">2000</text>
      <line x1="271" y1="260" x2="431" y2="123" stroke="#28a745" stroke-width="2"/>
      <line x1="271" y1="260" x2="439" y2="166" stroke="#dc3545" stroke-width="2"/>
    </svg>
  </section>

  <!-- plant -->
  <section class="card" style="left:607px;top:463px;width:288px;height:151px">
    <h3>Order 17746</h3>
    <div class="sub">Avg Cycle Time : 2 hrs 27 min</div>
    <span class="close" style="left:266px;top:10px">×</span>
    <div class="cat" style="color:var(--muted)"><svg width="17" height="14" style="color:#8a8f98"><use href="#factory"/></svg>Plant (min)</div>
    <div class="lbl" style="left:11px;top:88px">Planned</div>
    <div class="bar" style="left:60px;top:91px;width:139px;background:var(--blue)"></div>
    <div class="val" style="left:219px;top:86px">30</div>
    <div class="lbl" style="left:21px;top:110px">Actual</div>
    <div class="bar" style="left:60px;top:113px;width:174px;background:var(--red)"></div>
    <div class="val" style="left:254px;top:110px">33</div>
  </section>

  <!-- driving -->
  <section class="card" style="left:903px;top:463px;width:288px;height:151px">
    <h3>Order 17746</h3>
    <div class="sub">Avg Cycle Time : 2 hrs 27 min</div>
    <span class="close" style="left:272px;top:10px">×</span>
    <div class="cat"><svg width="21" height="15" style="color:#8a8f98"><use href="#truck"/></svg>Diving (min)</div>
    <div class="lbl" style="left:11px;top:88px">Planned</div>
    <div class="bar" style="left:60px;top:91px;width:104px;background:var(--yellow)"></div>
    <div class="val" style="left:174px;top:86px">60</div>
    <div class="lbl" style="left:20px;top:110px">Actual</div>
    <div class="bar" style="left:60px;top:113px;width:197px;background:var(--red)"></div>
    <div class="val" style="left:266px;top:110px">83</div>
  </section>

  <!-- jobsite -->
  <section class="card" style="left:607px;top:624px;width:288px;height:150px">
    <h3>Order 17746</h3>
    <div class="sub">Avg Cycle Time : 2 hrs 27 min</div>
    <span class="close" style="left:266px;top:10px">×</span>
    <div class="cat" style="left:14px"><svg width="12" height="16" style="color:#8a8f98"><use href="#pin"/></svg>Jobsite (min)</div>
    <div class="lbl" style="left:11px;top:88px">Planned</div>
    <div class="bar" style="left:60px;top:91px;width:139px;background:var(--green)"></div>
    <div class="val" style="left:209px;top:86px">30</div>
    <div class="lbl" style="left:21px;top:110px">Actual</div>
    <div class="bar" style="left:60px;top:113px;width:139px;background:var(--green)"></div>
    <div class="val" style="left:209px;top:110px">30</div>
  </section>

  <!-- equipment -->
  <section class="card" style="left:903px;top:624px;width:288px;height:150px">
    <h3>Order 17746</h3>
    <div class="sub">Avg Cycle Time : 2 hrs 27 min</div>
    <span class="close" style="left:272px;top:10px">×</span>
    <div class="cat" style="left:12px"><svg width="16" height="16" viewBox="0 0 16 16"><path d="M8 0l1.5 2.2 2.6-.6.6 2.6L15 5.6l-.8 2.4L15 10.4l-2.3 1.4-.6 2.6-2.6-.6L8 16l-1.5-2.2-2.6.6-.6-2.6L1 10.4 1.8 8 1 5.6l2.3-1.4.6-2.6 2.6.6z" fill="#8a8f98"/><circle cx="8" cy="8" r="2.6" fill="#fff"/></svg>Equipment (min)</div>
    <div class="lbl" style="left:11px;top:88px">Planned</div>
    <div class="bar" style="left:60px;top:91px;width:104px;background:var(--teal)"></div>
    <div class="val" style="left:174px;top:86px">60</div>
    <div class="lbl" style="left:20px;top:110px">Actual</div>
    <div class="bar" style="left:60px;top:113px;width:181px;background:var(--red)"></div>
    <div class="val" style="left:246px;top:110px">83</div>
  </section>
</div>
</body>
</html>
```